Corporate Business Card

Very professional, Modern, Not to busy, include phone address email, website
(253) 617-4930, 18761 52nd Avenue S, Kent, WA 98047, martin@plumlinegroup.com, varkoworks.com

Target Market(s)

Manufacturing

Industry/Entity Type

Aero, machining, manufacturing, Off road racing

Contact Information for Business Card

Phone, address email, website

```html
<!DOCTYPE html>
<html lang="en">
<head>
<meta charset="utf-8">
<title>Varko Works — Business Card</title>
<link href="https://fonts.googleapis.com/css2?family=Montserrat:wght@400;500;700&display=swap" rel="stylesheet">
<style>
  :root {
    --backdrop: #6c6c6c;
    --navy: #16346c;
    --red: #d4232b;
    --white: #ffffff;
    --ink: #1d1d1f;
  }
  * { box-sizing: border-box; margin: 0; padding: 0; }
  html, body { width: 1200px; height: 801px; overflow: hidden; }
  body {
    background: var(--backdrop);
    font-family: "Montserrat", sans-serif;
    display: flex;
    align-items: center;
    justify-content: center;
    gap: 40px;
  }
  .card {
    position: relative;
    width: 540px;
    height: 309px;
    border: 2px solid var(--red);
    overflow: hidden;
  }
  /* Front side */
  .card--front { background: var(--white); }
  .front-brand {
    position: absolute;
    left: 36px;
    top: 126px;
    width: 216px;
  }
  .brand-name {
    display: flex;
    align-items: center;
    gap: 8px;
    color: var(--navy);
    font-weight: 700;
    font-size: 22px;
    letter-spacing: 0.5px;
    text-transform: uppercase;
    line-height: 1;
    white-space: nowrap;
  }
  .brand-mark {
    width: 11px;
    height: 11px;
    background: var(--red);
    flex: none;
  }
  .brand-rule {
    margin-top: 14px;
    height: 1.5px;
    width: 150px;
    background: var(--navy);
  }
  .divider {
    position: absolute;
    left: 262px;
    top: 40px;
    width: 1.5px;
    height: 228px;
    background: var(--red);
  }
  .contact {
    position: absolute;
    left: 284px;
    top: 48px;
    right: 16px;
    color: var(--ink);
    font-size: 13px;
    line-height: 1.45;
    white-space: nowrap;
  }
  .contact__name {
    color: var(--red);
    font-weight: 700;
    font-size: 19px;
    letter-spacing: 0.5px;
    text-transform: uppercase;
    line-height: 1.2;
  }
  .contact__title { margin-bottom: 14px; }
  .contact__address { margin-bottom: 14px; }
  .contact__row { display: flex; align-items: center; gap: 7px; }
  .contact__row svg { width: 11px; height: 11px; flex: none; }

  /* Back side */
  .card--back { background: var(--navy); }
  .back-brand {
    position: absolute;
    left: 58px;
    top: 106px;
  }
  .back-brand .brand-name {
    color: var(--white);
    font-size: 44px;
    gap: 14px;
  }
  .back-brand .brand-mark { width: 20px; height: 20px; }
  .back-brand .brand-rule {
    margin-top: 24px;
    width: 230px;
    height: 2px;
    background: var(--white);
  }
</style>
</head>
<body>

  <section class="card card--front" aria-label="Business card front">
    <div class="front-brand">
      <div class="brand-name"><span class="brand-mark"></span>Varko Works</div>
      <div class="brand-rule"></div>
    </div>
    <div class="divider"></div>
    <div class="contact">
      <p class="contact__name">Daniel Hargrove</p>
      <p class="contact__title">Owner/CEO</p>
      <p class="contact__address">18761 52nd<br>Avenue S, Kent, WA 98047</p>
      <p class="contact__row">
        <svg viewBox="0 0 12 12" aria-hidden="true"><path fill="#d4232b" d="M2.4 0.8l2 2-1 1.3a7 7 0 0 0 4.5 4.5l1.3-1 2 2-1.4 1.6C5.4 11 1 6.6 0.8 2.2z"/></svg>
        (253) 617-4930
      </p>
      <p class="contact__row">
        <svg viewBox="0 0 12 12" aria-hidden="true"><rect x="0.5" y="2" width="11" height="8" fill="#d4232b"/><path d="M0.5 2l5.5 4.5L11.5 2" fill="none" stroke="#fff" stroke-width="1"/></svg>
        martin@plumlinegroup.com
      </p>
      <p class="contact__row">
        <svg viewBox="0 0 12 12" aria-hidden="true"><circle cx="6" cy="6" r="5.5" fill="#d4232b"/><path d="M0.5 6h11M6 0.5c-2.5 3-2.5 8 0 11M6 0.5c2.5 3 2.5 8 0 11" fill="none" stroke="#fff" stroke-width="0.7"/></svg>
        www.varkoworks.com
      </p>
    </div>
  </section>

  <section class="card card--back" aria-label="Business card back">
    <div class="back-brand">
      <div class="brand-name"><span class="brand-mark"></span>Varko Works</div>
      <div class="brand-rule"></div>
    </div>
  </section>

</body>
</html>
```